Acupuncture business needs business card design

I need a business card for an acupuncture clinic called "Harbourlight Wellness"
It will need the following details:
My name: Marcus Pelling
Acupuncturist
Member TVBH
KWF Treatment Provider
Ph numbers: 581 2734 027 418 5620
Email: marcus@hbwel.example.nz
On the back it will need a table with 2 columns for appointments, one column for time and one for date.

Industry/Entity Type

Clinic

Contact Information for Business Card

Marcus Pelling
Acupuncturist
Member TVBH
KWF Treatment Provider
Email: marcus@hbwel.example.nz

Requirements
Must have
• Marcus Pelling
• Acupuncturist
• Member TVBH
• KWF Treatment Provider
• Ph numbers: 581 2734 027 418 5620
• Email: marcus@hbwel.example.nz
• On the back it will need a table with 2 columns for appointments, one column for time and one for date.

```html
<!DOCTYPE html>
<html lang="en">
<head>
<meta charset="utf-8">
<title>Harbourlight Wellness – Business Card</title>
<link href="https://fonts.googleapis.com/css2?family=Open+Sans:wght@400;600;700&family=Open+Sans+Condensed:wght@700&display=swap" rel="stylesheet">
<style>
  :root {
    --teal: #157f97;
    --sky: #29a9d8;
    --sky-light: #6cc6e8;
    --ink: #4a4f55;
    --paper: #ffffff;
    --backdrop: #e9ecee;
    --line: #8a8f94;
  }
  html, body {
    margin: 0;
    width: 1200px;
    height: 948px;
    overflow: hidden;
    background: var(--backdrop);
    font-family: "Open Sans", Arial, sans-serif;
  }
  .sheet {
    width: 1200px;
    height: 948px;
    display: flex;
    flex-direction: column;
    align-items: center;
    justify-content: center;
    gap: 48px;
  }
  .card {
    position: relative;
    width: 700px;
    height: 400px;
    background: var(--paper);
    box-shadow: 0 2px 10px rgba(0,0,0,0.12);
    overflow: hidden;
  }
  .brand {
    position: absolute;
    display: flex;
    align-items: center;
    gap: 14px;
  }
  .brand-dot {
    width: 44px;
    height: 44px;
    border-radius: 50%;
    background: var(--teal);
    flex: none;
  }
  .brand-name {
    font-family: "Open Sans Condensed", "Open Sans", sans-serif;
    font-weight: 700;
    font-size: 40px;
    line-height: 1;
    color: var(--sky);
    letter-spacing: 0.5px;
  }
  .brand-tagline {
    font-size: 11px;
    letter-spacing: 4.4px;
    color: var(--teal);
    margin-top: 4px;
  }
  /* front */
  .front .brand { left: 250px; top: 40px; }
  .holder {
    position: absolute;
    left: 44px;
    top: 96px;
  }
  .holder-name {
    font-weight: 700;
    font-size: 20px;
    line-height: 1.3;
    color: var(--teal);
    margin: 0 0 4px;
  }
  .holder-role {
    font-size: 13px;
    line-height: 1.45;
    color: var(--sky);
    margin: 0;
  }
  .wave {
    position: absolute;
    left: 0;
    top: 0;
  }
  .contact {
    position: absolute;
    left: 44px;
    bottom: 16px;
    color: var(--paper);
    font-size: 14px;
    line-height: 24px;
  }
  .contact-line {
    display: flex;
    align-items: center;
    gap: 8px;
  }
  .contact-line svg { flex: none; }
  .address { font-size: 14px; }
  /* back */
  .back .brand { left: 150px; top: 40px; }
  .appointments {
    position: absolute;
    left: 70px;
    top: 140px;
    border-collapse: separate;
    border-spacing: 14px 10px;
  }
  .appointments th {
    font-weight: 400;
    font-size: 16px;
    color: var(--ink);
    text-align: left;
    padding: 0 0 0 2px;
  }
  .appointments td {
    border: 1.5px solid var(--line);
    height: 30px;
    padding: 0;
  }
  .col-date { width: 180px; }
  .col-time { width: 330px; }
  .website {
    position: absolute;
    left: 84px;
    bottom: 36px;
    font-size: 17px;
    letter-spacing: 4px;
    color: var(--ink);
  }
</style>
</head>
<body>
<main class="sheet">

  <section class="card front" aria-label="Card front">
    <svg class="wave" width="700" height="400" viewBox="0 0 700 400" aria-hidden="true">
      <path d="M0 230 C200 225 330 300 450 330 S620 372 700 368 L700 400 L0 400 Z" fill="var(--teal)"/>
      <path d="M0 212 C200 207 330 282 450 312 S620 354 700 350" fill="none" stroke="var(--sky)" stroke-width="9"/>
      <path d="M0 198 C200 193 330 268 450 298 S620 340 700 336" fill="none" stroke="var(--sky-light)" stroke-width="2.5"/>
    </svg>

    <div class="brand">
      <span class="brand-dot"></span>
      <div>
        <div class="brand-name">Harbourlight Wellness</div>
        <div class="brand-tagline">ACUPUNCTURE PHYSIOTHERAPY</div>
      </div>
    </div>

    <div class="holder">
      <p class="holder-name">Marcus Pelling</p>
      <p class="holder-role">Acupuncturist, Member TVBH<br>KWF Treatment Provider</p>
    </div>

    <div class="contact">
      <div class="contact-line">
        <svg width="16" height="16" viewBox="0 0 16 16" aria-hidden="true"><circle cx="8" cy="8" r="7.2" fill="none" stroke="#fff" stroke-width="1.4"/><path d="M5.2 4.4c.5-.4 1-.3 1.3.2l.6 1c.2.4.1.8-.2 1l-.4.3c.4.9 1 1.5 1.9 1.9l.3-.4c.3-.3.7-.4 1-.2l1 .6c.5.3.6.8.2 1.3-.6.8-1.5 1-2.4.6-1.8-.8-3-2-3.8-3.8-.4-.9-.2-1.8.5-2.5z" fill="#fff"/></svg>
        <span>581 2734 / 027 418 5620</span>
      </div>
      <div class="contact-line">
        <svg width="16" height="16" viewBox="0 0 16 16" aria-hidden="true"><circle cx="8" cy="8" r="8" fill="#fff"/><rect x="4" y="5.2" width="8" height="5.6" fill="none" stroke="var(--teal)" stroke-width="1.1"/><path d="M4 5.4 8 8.6 12 5.4" fill="none" stroke="var(--teal)" stroke-width="1.1"/></svg>
        <span>marcus@hbwel.example.nz</span>
      </div>
      <div class="address">Street Name, City Name Zipcode-01234</div>
    </div>
  </section>

  <section class="card back" aria-label="Card back">
    <div class="brand">
      <span class="brand-dot"></span>
      <div>
        <div class="brand-name">Harbourlight Wellness</div>
        <div class="brand-tagline">ACUPUNCTURE PHYSIOTHERAPY</div>
      </div>
    </div>

    <table class="appointments">
      <thead>
        <tr><th class="col-date">Date</th><th class="col-time">Time</th></tr>
      </thead>
      <tbody>
        <tr><td></td><td></td></tr>
        <tr><td></td><td></td></tr>
        <tr><td></td><td></td></tr>
      </tbody>
    </table>

    <div class="website">www.hbwel.example.nz</div>
  </section>

</main>
</body>
</html>
```